Fresh, modern, fun business card for pediatric dental practice

Need a business card for fresh, modern, fun pediatric dental practice

Clean look that matches our website's font and colors

We prefer the look of curved corners on business cards

Target Market(s)

parents (mothers) of young children, professionals, mid-high class

Industry/Entity Type

Dental

Contact Information for Business Card

Maplebrook Pediatric Dentistry
482 Quarry Lane
Suite 517
Alderton, PA 10000
717.555.0193
www.maplebrookkidsdental.example

Mei-Ran Tsai, DMD
Corinne Walbeck, DMD
(we are working on our email address, but we would like that on the card as well)

Font styles to use
Sans Serif

Requirements
Must have
• All info; we would also like to make cards for individual staff members
• colors from our website and color palatte, attatched
• use same font and design as website for branding
Nice to have
• clean, simple card that has a pop of color
• we would like to see a few designs with our tag line "where smiles get brighter"
• we are not sure if we want to have it on there or not
• we would like to see a few designs incorporating the ribbon graphic on our website where the word WELCOME is

```html
<!DOCTYPE html>
<html lang="en">
<head>
<meta charset="utf-8">
<title>Maplebrook Pediatric Dentistry – Business Card</title>
<link rel="stylesheet" href="https://fonts.googleapis.com/css2?family=Montserrat:wght@500;600&family=Lato:wght@400&display=swap">
<style>
  :root {
    --page-bg: #e6e3df;
    --card-black: #0e0e0e;
    --sun-yellow: #f6b71c;
    --berry-pink: #d2309a;
    --text-white: #f2f2f2;
    --silver: #c9c9c9;
  }
  * { box-sizing: border-box; margin: 0; padding: 0; }
  html, body { width: 1200px; height: 900px; overflow: hidden; }
  body {
    background: var(--page-bg);
    display: flex;
    align-items: center;
    justify-content: center;
    gap: 60px;
  }
  .card {
    position: relative;
    width: 525px;
    height: 300px;
    background: var(--card-black);
    border-radius: 18px;
    box-shadow: 0 10px 30px rgba(0,0,0,.25);
    color: var(--text-white);
  }
  /* Front: contact side */
  .brand {
    position: absolute;
    top: 34px;
    right: 34px;
    display: flex;
    align-items: center;
    gap: 12px;
  }
  .brand-dot {
    width: 26px; height: 26px;
    border-radius: 50%;
    background: var(--sun-yellow);
    flex: none;
  }
  .brand-name {
    font-family: "Montserrat", sans-serif;
    font-weight: 600;
    font-size: 22px;
    line-height: 1.15;
    color: var(--sun-yellow);
    text-align: right;
  }
  .doctors {
    position: absolute;
    left: 30px;
    top: 150px;
    font-family: "Montserrat", sans-serif;
    font-weight: 500;
    font-size: 18px;
    line-height: 1.35;
  }
  .doctor-primary { color: var(--sun-yellow); }
  .doctor-secondary { color: var(--berry-pink); }
  .contact-list {
    position: absolute;
    left: 30px;
    top: 210px;
    list-style: none;
    font-family: "Lato", sans-serif;
    font-size: 12.5px;
    line-height: 1.5;
  }
  .contact-list li { display: flex; align-items: center; gap: 7px; }
  .contact-list svg { width: 11px; height: 11px; fill: var(--sun-yellow); flex: none; }
  .address {
    position: absolute;
    right: 30px;
    top: 150px;
    font-family: "Lato", sans-serif;
    font-style: normal;
    font-size: 12.5px;
    line-height: 1.45;
    text-align: right;
  }
  /* Back: brand side */
  .card-back {
    display: flex;
    flex-direction: column;
    align-items: center;
    justify-content: center;
    gap: 18px;
  }
  .back-dot {
    width: 40px; height: 40px;
    border-radius: 50%;
    border: 2px solid var(--silver);
  }
  .back-name {
    font-family: "Montserrat", sans-serif;
    font-weight: 600;
    font-size: 26px;
    color: var(--silver);
    letter-spacing: .5px;
    text-align: center;
    line-height: 1.2;
  }
</style>
</head>
<body>
  <section class="card card-front">
    <div class="brand">
      <div class="brand-name">Maplebrook<br>Pediatric Dentistry</div>
      <span class="brand-dot"></span>
    </div>

    <div class="doctors">
      <p class="doctor-primary">Mei-Ran Tsai, DMD</p>
      <p class="doctor-secondary">Corinne Walbeck, DMD</p>
    </div>

    <ul class="contact-list">
      <li>
        <svg viewBox="0 0 16 16" aria-hidden="true"><path d="M3.5 1l2.5 3-1.5 2c1 2 3 4 5 5l2-1.5 3 2.5-1.5 2.5C7 14.5 1.5 9 1 3z"/></svg>
        717.555.0193
      </li>
      <li>
        <svg viewBox="0 0 16 16" aria-hidden="true"><path d="M1 3h14v10H1z M2 4l6 5 6-5" stroke="#0e0e0e" stroke-width="1.2"/></svg>
        mei-ran@maplebrookkidsdental.example
      </li>
      <li>
        <svg viewBox="0 0 16 16" aria-hidden="true"><path d="M1 3h14v10H1z M2 4l6 5 6-5" stroke="#0e0e0e" stroke-width="1.2"/></svg>
        corinne@maplebrookkidsdental.example
      </li>
      <li>
        <svg viewBox="0 0 16 16" aria-hidden="true"><circle cx="8" cy="8" r="7"/><path d="M1 8h14M8 1c-3 3-3 11 0 14M8 1c3 3 3 11 0 14" stroke="#0e0e0e" stroke-width="1" fill="none"/></svg>
        www.maplebrookkidsdental.example
      </li>
    </ul>

    <address class="address">
      Maplebrook Pediatric Dentistry<br>
      482 Quarry Lane<br>
      Suite 517 Alderton, PA 10000
    </address>
  </section>

  <section class="card card-back">
    <span class="back-dot"></span>
    <p class="back-name">Maplebrook<br>Pediatric Dentistry</p>
  </section>
</body>
</html>
```